Salon and Spa Distributor Business Card

Need a business card. We are are distributor in the salon and spa industry. We identify with natural beauty. Need a card with:
Company Name: Petal Quarry"
Title: "President & CEO"
Address
Company Phone number
email
website
Tag Line:" The Professional Salon Source"

Industry/Entity Type

Business

Contact Information for Business Card

Name: Dov Strommen
Title: "President & CEO"
Address: 31 Harlow Ln, Bexmoor, NJ 07813
Company Phone number: 800-463-5918
email: dovstrommen@petalquarry.example
website: www.petalquarry.example

Requirements
Should not have
• No black backgrounds

```html
<!DOCTYPE html>
<html lang="en">
<head>
<meta charset="utf-8">
<title>Petal Quarry — Business Card</title>
<link rel="stylesheet" href="https://fonts.googleapis.com/css2?family=Mulish:wght@300;400;700&display=swap">
<style>
  :root {
    --stage: #e6e6e6;
    --green-deep: #005c29;
    --green-mid: #1f6f35;
    --green-soft: #357f42;
    --green-bright: #47ad2f;
    --paper: #f4f4f4;
    --paper-edge: #e9e9e9;
    --ink: #4a4a4a;
    --white: #ffffff;
    --white-soft: rgba(255,255,255,0.85);
  }
  html, body {
    margin: 0;
    padding: 0;
    width: 1200px;
    height: 576px;
    overflow: hidden;
    background: var(--stage);
    font-family: "Mulish", sans-serif;
  }
  .sheet {
    position: relative;
    width: 1200px;
    height: 576px;
  }
  .card {
    position: absolute;
    top: 138px;
    width: 484px;
    height: 294px;
    border-radius: 13px;
    overflow: hidden;
    box-shadow: 0 2px 5px rgba(0,0,0,0.18);
  }

  /* Front */
  .card--front {
    left: 82px;
    background: linear-gradient(180deg, var(--green-deep) 0%, var(--green-mid) 55%, var(--green-soft) 100%);
  }
  .brand-block {
    position: absolute;
    left: 0;
    right: 0;
    top: 118px;
    text-align: center;
    color: var(--white);
  }
  .brand {
    display: flex;
    align-items: center;
    justify-content: center;
    gap: 10px;
    font-weight: 300;
    font-size: 28px;
    line-height: 34px;
    letter-spacing: 0.2px;
  }
  .brand__dot {
    width: 12px;
    height: 12px;
    border-radius: 50%;
    background: var(--white);
  }
  .tagline {
    margin: 6px 0 0;
    font-weight: 300;
    font-size: 12px;
    letter-spacing: 1px;
    color: var(--white-soft);
  }

  /* Back */
  .card--back {
    left: 602px;
    width: 482px;
    background: linear-gradient(180deg, var(--paper) 0%, var(--paper-edge) 100%);
  }
  .back__panel {
    position: absolute;
    left: 0;
    top: 0;
    width: 482px;
    height: 294px;
  }
  .card--back .brand-block {
    right: auto;
    width: 206px;
    top: 120px;
  }
  .card--back .brand {
    font-size: 25px;
    line-height: 30px;
    gap: 8px;
  }
  .card--back .brand__dot { width: 10px; height: 10px; }
  .card--back .tagline {
    font-size: 10.5px;
    letter-spacing: 0.6px;
  }
  .identity {
    position: absolute;
    right: 24px;
    top: 37px;
    text-align: right;
  }
  .identity__name {
    margin: 0;
    font-weight: 700;
    font-size: 18px;
    color: var(--green-deep);
  }
  .identity__title {
    margin: 3px 0 0;
    font-size: 10.5px;
    color: var(--ink);
  }
  .contact {
    position: absolute;
    right: 22px;
    top: 186px;
    margin: 0;
    padding: 0;
    list-style: none;
    text-align: right;
    font-size: 12.5px;
    color: var(--ink);
  }
  .contact__item {
    display: flex;
    justify-content: flex-end;
    align-items: center;
    gap: 6px;
    height: 18px;
  }
  .contact__item--address { margin-top: 3px; }
  .contact__icon {
    width: 10px;
    height: 10px;
    fill: var(--green-deep);
  }
  .contact__spacer { width: 10px; }
</style>
</head>
<body>
<main class="sheet">
  <section class="card card--front" aria-label="Card front">
    <div class="brand-block">
      <div class="brand"><span class="brand__dot"></span><span>Petal Quarry</span></div>
      <p class="tagline">The Professional Salon Source</p>
    </div>
  </section>

  <section class="card card--back" aria-label="Card back">
    <svg class="back__panel" viewBox="0 0 482 294" aria-hidden="true">
      <path d="M0 0 H214 C206 60 232 120 226 180 C222 230 208 265 194 294 H0 Z" fill="var(--green-bright)"/>
      <path d="M0 0 H208 C200 60 226 120 220 180 C216 230 202 265 188 294 H0 Z" fill="var(--green-deep)"/>
    </svg>
    <div class="brand-block">
      <div class="brand"><span class="brand__dot"></span><span>Petal Quarry</span></div>
      <p class="tagline">The Professional Salon Source</p>
    </div>

    <div class="identity">
      <p class="identity__name">Dov Strommen</p>
      <p class="identity__title">President &amp; CEO</p>
    </div>

    <ul class="contact">
      <li class="contact__item">800-463-5918
        <svg class="contact__icon" viewBox="0 0 10 10"><path d="M1 3 C1 1.5 9 1.5 9 3 L8 4.2 6.6 3.4 6.6 2.6 H3.4 V3.4 L2 4.2 Z M2.2 5 H7.8 L8.6 9 H1.4 Z"/></svg>
      </li>
      <li class="contact__item">www.petalquarry.example
        <svg class="contact__icon" viewBox="0 0 10 10"><path d="M0.5 2 H9.5 V8 H0.5 Z M1 2.4 L5 5.6 9 2.4" stroke="var(--paper)" stroke-width="0.8"/></svg>
      </li>
      <li class="contact__item">dovstrommen@petalquarry.example
        <svg class="contact__icon" viewBox="0 0 10 10"><circle cx="5" cy="5" r="4.6"/><path d="M0.5 5 H9.5 M5 0.5 V9.5 M5 0.5 C2.5 3 2.5 7 5 9.5 M5 0.5 C7.5 3 7.5 7 5 9.5" stroke="var(--paper)" stroke-width="0.7" fill="none"/></svg>
      </li>
      <li class="contact__item contact__item--address">31 Harlow Ln, Bexmoor, NJ 07813<span class="contact__spacer"></span></li>
    </ul>
  </section>
</main>
</body>
</html>
```